SnackOrbit!!! A Vending Machine Business Looking for an attractive website.

We are a vending machine business in Northern Michigan. We have changed our name and have rebranded our company. We would like an attractive website that shares who we are, what services we provide, the products we offer in our machines, along with a form businesses can fill out to see if they are a good fit for our company. I would like to have a Home Page, About SnackOrbit, Why Choose SnackOrbit?, Products & Services, Contact Us (With a Login Option), and a page with a questionnaire for thos interested in getting a FREE Vending Machine.

Target Market(s)

Businesses, Campgrounds, Schools, and many more in Northern Michigan

Industry/Entity Type

Vending Machines

Coding

Coded - Design and coding required

Number of Pages Required

5+ page

Requirements
Must have
• An inviting and enticing Home Page. I want to get my potential clients engaged in our website.
Nice to have
• Possibly background photos from Northern Michigan
Should not have
• A corporate feel. I do not want a boring website.

```html
<!DOCTYPE html>
<html lang="en">
<head>
<meta charset="utf-8">
<title>SnackOrbit – Crave. Vend. Repeat.</title>
<link href="https://fonts.googleapis.com/css2?family=Comic+Neue:wght@700&family=Roboto:wght@400;500;700&display=swap" rel="stylesheet">
<style>
:root{
  --purple:#2a1a5e;
  --purple-deep:#1d1145;
  --lavender:#f3f1fd;
  --green:#23531f;
  --green-band:#2c5c25;
  --ink:#222;
  --muted:#555;
  --white:#fff;
  --black:#0e0e11;
}
*{box-sizing:border-box;margin:0;padding:0}
html,body{width:1200px;height:4577px;overflow:hidden}
body{font-family:"Roboto",sans-serif;color:var(--ink);background:var(--white);position:relative}
.abs{position:absolute}
.display{font-family:"Comic Neue",cursive;font-weight:700;text-transform:uppercase;letter-spacing:1px;color:var(--purple)}
.btn{position:absolute;background:var(--green);color:var(--white);font:700 15px "Roboto",sans-serif;text-transform:uppercase;display:flex;align-items:center;justify-content:center}
.photo{position:absolute}

/* header */
.brand{position:absolute;left:112px;top:30px;display:flex;align-items:center;gap:10px;font:700 40px "Roboto",sans-serif;color:var(--purple)}
.brand-dot{width:34px;height:34px;border-radius:50%;background:var(--green)}
.contact-chip{position:absolute;top:34px;display:flex;align-items:center;gap:14px}
.chip-icon{width:52px;height:52px;border-radius:50%;background:var(--white);box-shadow:0 3px 12px rgba(0,0,0,.15);display:flex;align-items:center;justify-content:center}
.chip-label{font-size:11px;color:var(--muted);font-weight:500}
.chip-value{font-size:15px;color:var(--ink);font-weight:500;margin-top:4px}
.social{display:flex;gap:8px}
.social span{width:36px;height:36px;border-radius:50%;border:1px solid #ccc;display:block;background:var(--white)}
.social span.filled{background:var(--green);border-color:var(--green)}
.nav{position:absolute;top:118px;left:0;width:1200px;height:54px;background:var(--purple)}
.nav a{position:absolute;top:19px;font:500 14px "Roboto",sans-serif;color:var(--white);text-decoration:none;text-transform:uppercase}
.nav a.current{color:#3f7d2f}

/* hero */
.hero{position:absolute;top:172px;left:0;width:1200px;height:686px;overflow:hidden;
  background:
    linear-gradient(180deg,rgba(0,0,0,0) 40%,rgba(0,0,0,.25) 100%),
    radial-gradient(ellipse 260px 300px at 1080px 330px,#8c3f2c 0%,rgba(140,63,44,0) 100%),
    radial-gradient(ellipse 220px 340px at 120px 300px,#6d5a4c 0%,rgba(109,90,76,0) 100%),
    radial-gradient(ellipse 360px 120px at 600px 260px,#5a7a4a 0%,rgba(90,122,74,0) 100%),
    radial-gradient(ellipse 300px 200px at 600px 560px,#77706a 0%,rgba(119,112,106,0) 100%),
    linear-gradient(180deg,#3f73b0 0%,#7ea6cc 22%,#a9b9c1 34%,#8a7564 52%,#6e625a 75%,#5a524c 100%)}
.hero-title{position:absolute;top:170px;width:100%;text-align:center;font-size:56px;line-height:58px;color:var(--white);text-shadow:0 2px 8px rgba(0,0,0,.35)}
.hero-sub{position:absolute;top:304px;width:100%;text-align:center;font-size:28px;color:var(--white);font-weight:500;text-shadow:0 2px 6px rgba(0,0,0,.4)}

/* who */
.who-text{position:absolute;left:686px;top:1024px;width:402px;font-size:15.5px;line-height:27.5px;color:var(--muted);text-align:justify}

/* services */
.services{position:absolute;top:1481px;left:0;width:1200px;height:654px;background:var(--lavender)}
.svc-card{position:absolute;top:164px;width:302px;height:405px;background:var(--white);box-shadow:0 6px 18px rgba(80,70,160,.25)}
.svc-card .photo{left:7px;top:7px;width:288px;height:216px}
.svc-card h3{position:absolute;top:246px;width:100%;text-align:center;font-size:17px;font-weight:500;color:var(--ink)}
.svc-card p{position:absolute;top:282px;left:24px;right:24px;text-align:center;font-size:13.5px;line-height:23px;color:var(--muted)}
.svc-card .more{position:absolute;top:361px;width:100%;text-align:center;font-size:14px;font-weight:700;color:var(--green);text-decoration:underline}

/* products */
.products{position:absolute;top:2135px;left:0;width:1200px;height:528px;background:radial-gradient(ellipse at 30% 40%,#35692b,var(--green-band) 60%,#224a1d)}
.prod-card{position:absolute;top:169px;width:224px;height:252px;background:var(--white)}
.prod-card .machine{position:absolute;left:76px;top:24px;width:72px;height:132px;border-radius:3px}
.prod-card h3{position:absolute;top:176px;width:100%;text-align:center;font-size:17px;font-weight:500;color:var(--purple)}
.prod-card p{position:absolute;top:205px;left:10px;right:10px;text-align:center;font-size:13.5px;line-height:23px;color:var(--ink)}

/* why */
.why-text{position:absolute;left:112px;top:2800px;width:488px;font-size:15.5px;line-height:27px;color:var(--muted);text-align:justify}
.why-text p+p{margin-top:12px}

/* contact */
.field{position:absolute;height:46px;background:var(--white);box-shadow:0 4px 12px rgba(90,80,170,.2);font-size:13px;color:#777;padding:14px 16px}

/* cta */
.cta{position:absolute;top:3717px;left:0;width:1200px;height:540px;
  background:
    radial-gradient(ellipse 300px 200px at 180px 300px,rgba(120,60,140,.45),rgba(120,60,140,0)),
    radial-gradient(ellipse 260px 180px at 1020px 260px,rgba(90,70,170,.45),rgba(90,70,170,0)),
    linear-gradient(180deg,#2a1a60,#1e1146 70%,#1a1040)}
.cta h2{position:absolute;top:92px;width:100%;text-align:center;font-size:44px;line-height:50px;color:var(--white)}
.cta p{position:absolute;top:218px;left:200px;width:800px;text-align:center;font-size:17px;line-height:28px;color:var(--white)}

/* footer */
.footer{position:absolute;top:4100px;left:0;width:1200px;height:477px;background:var(--black);color:var(--white)}
.f-head{position:absolute;top:190px;font-size:17px;font-weight:500}
.f-link{position:absolute;font-size:14px;display:flex;align-items:center;gap:12px}
.f-tick{width:12px;height:12px;border-radius:50%;background:var(--green)}
.f-contact{position:absolute;left:112px;display:flex;align-items:center;gap:20px;font-size:14px}
.f-contact .ic{width:36px;height:36px;border-radius:50%;background:var(--white)}
.f-social{position:absolute;left:810px;top:338px;display:flex;gap:8px}
.f-social span{width:38px;height:38px;border-radius:50%;background:var(--white);display:block}
.pay{position:absolute;top:440px;width:40px;height:22px;background:#d9d9d9;border-radius:3px}
</style>
</head>
<body>

<!-- header -->
<div class="brand"><span class="brand-dot"></span>SnackOrbit</div>
<div class="contact-chip" style="left:490px">
  <div class="chip-icon"><svg width="22" height="22" viewBox="0 0 24 24"><path d="M6.6 10.8a15 15 0 006.6 6.6l2.2-2.2a1 1 0 011-.25 11.4 11.4 0 003.6.57 1 1 0 011 1V20a1 1 0 01-1 1A17 17 0 013 4a1 1 0 011-1h3.5a1 1 0 011 1c0 1.25.2 2.45.57 3.57a1 1 0 01-.25 1z" fill="#23531f"/></svg></div>
  <div><div class="chip-label">CALL US:</div><div class="chip-value">+1 (555) 010 0199</div></div>
</div>
<div class="contact-chip" style="left:715px">
  <div class="chip-icon"><svg width="22" height="22" viewBox="0 0 24 24"><rect x="3" y="6" width="18" height="13" rx="1" fill="#23531f"/><path d="M3 7l9 6 9-6" stroke="#fff" stroke-width="1.6" fill="none"/></svg></div>
  <div><div class="chip-label">EMAIL US:</div><div class="chip-value">hello@snackorbit.com</div></div>
</div>
<div class="social abs" style="left:966px;top:42px"><span class="filled"></span><span></span><span></span></div>

<nav class="nav">
  <a class="current" style="left:110px">Home</a>
  <a style="left:195px">About SnackOrbit</a>
  <a style="left:376px">Why Choose SnackOrbit?</a>
  <a style="left:610px">Products &amp; Services</a>
  <a style="left:812px">Contact Us</a>
  <a style="left:1046px;font-weight:700">
    <svg width="16" height="14" viewBox="0 0 24 20" style="vertical-align:-2px"><path d="M1 1h4l3 12h12l3-9H7" stroke="#fff" stroke-width="2.4" fill="none"/><circle cx="10" cy="17" r="2" fill="#fff"/><circle cx="18" cy="17" r="2" fill="#fff"/></svg> (0)</a>
</nav>

<!-- hero -->
<section class="hero" role="img" aria-label="Northern Michigan small-town main street with brick buildings, a clock tower and wooded hills under a blue sky">
  <h1 class="hero-title display">SnackOrbit: Crave.<br>Vend. Repeat.</h1>
  <div class="hero-sub">Elevating Snacking, One Vend at a Time</div>
  <div class="btn" style="left:530px;top:368px;width:138px;height:46px;font-size:14px">Get a Quote</div>
  <svg class="abs" style="left:0;top:0" width="1200" height="686" viewBox="0 0 1200 686">
    <polygon points="110,686 1200,545 1200,686" fill="#efeafd"/>
    <polygon points="0,686 0,660 600,628 1200,532 1200,686" fill="#fff"/>
    <polygon points="600,628 1200,532 1200,686 820,686" fill="#2a1a5e"/>
  </svg>
</section>

<!-- who we are -->
<div class="photo" style="left:304px;top:933px;width:322px;height:235px;background:radial-gradient(ellipse 90px 120px at 180px 140px,#c9a27c,rgba(201,162,124,0)),radial-gradient(ellipse 90px 110px at 70px 110px,#d8cfc6,rgba(216,207,198,0)),linear-gradient(90deg,#8a949c 0%,#c7cdd2 45%,#3d4650 80%,#1f2630 100%)" role="img" aria-label="Young couple choosing snacks at a vending machine"></div>
<div class="photo" style="left:112px;top:1053px;width:288px;height:195px;background:radial-gradient(ellipse 70px 90px at 70px 90px,#d9b79a,rgba(217,183,154,0)),linear-gradient(90deg,#f1eeea 0%,#d8d2cc 30%,#3a3a3e 55%,#c63a3a 62%,#2d2d30 70%,#b9b7bd 100%)" role="img" aria-label="Two women smiling beside a vending machine"></div>
<div class="photo" style="left:304px;top:1147px;width:265px;height:203px;background:radial-gradient(ellipse 80px 70px at 90px 80px,#c98a5a,rgba(201,138,90,0)),radial-gradient(ellipse 70px 80px at 190px 60px,#2a2a2e,rgba(42,42,46,0)),linear-gradient(160deg,#8fbbe0 0%,#3b79b0 50%,#e9ecef 100%)" role="img" aria-label="Group of friends picking snacks from a vending machine"></div>
<h2 class="display abs" style="left:686px;top:946px;font-size:46px">Who We Are</h2>
<p class="who-text">Welcome to SnackOrbit, where snacking meets delight! We're not just about vending machines; we're your culinary companions, your flavor curators, and your secret stash of happiness. Daniel and Nora, the dynamic duo behind SnackOrbit, have a passion for all things tasty. With backgrounds in sales and a penchant for personal connections, they've transformed the vending experience into an art form.</p>
<div class="btn" style="left:686px;top:1273px;width:137px;height:51px">Learn More</div>

<!-- services -->
<section class="services">
  <h2 class="display abs" style="top:72px;width:100%;text-align:center;font-size:46px">Our Services</h2>
  <div class="svc-card" style="left:112px"><div class="photo" role="img" aria-label="Woman selecting a drink from a glass-front vending machine" style="background:radial-gradient(ellipse 70px 100px at 230px 110px,#e8ded2,rgba(232,222,210,0)),radial-gradient(ellipse 60px 80px at 90px 110px,#d9c9a8,rgba(217,201,168,0)),linear-gradient(90deg,#2a2a2a 0%,#6b6660 30%,#c4bfb6 55%,#6e6a3a 80%,#4a4a2c 100%)"></div><h3>LOREM IPSUM DOLOR</h3><p>Lorem ipsum dolor sit amet, consectetur adipiscing elit, sed do eiusmod tempor incididunt ut laborea.</p><div class="more">READ MORE</div></div>
  <div class="svc-card" style="left:448px"><div class="photo" role="img" aria-label="Student using a snack vending machine in a hallway" style="background:radial-gradient(ellipse 60px 90px at 80px 130px,#7a2a2a,rgba(122,42,42,0)),radial-gradient(ellipse 70px 100px at 170px 110px,#5a7a9a,rgba(90,122,154,0)),linear-gradient(90deg,#9a9ea2 0%,#6c7076 40%,#2b3340 70%,#1a1c22 100%)"></div><h3>LOREM IPSUM DOLOR</h3><p>Lorem ipsum dolor sit amet, consectetur adipiscing elit, sed do eiusmod tempor incididunt ut laborea.</p><div class="more">READ MORE</div></div>
  <div class="svc-card" style="left:785px"><div class="photo" role="img" aria-label="Travelers buying snacks from a vending machine at a station" style="background:radial-gradient(ellipse 60px 90px at 80px 120px,#4a6a9a,rgba(74,106,154,0)),radial-gradient(ellipse 60px 80px at 180px 80px,#c8703a,rgba(200,112,58,0)),linear-gradient(90deg,#5c5a60 0%,#8c8a90 40%,#3a3c44 70%,#e05a30 100%)"></div><h3>LOREM IPSUM DOLOR</h3><p>Lorem ipsum dolor sit amet, consectetur adipiscing elit, sed do eiusmod tempor incididunt ut laborea.</p><div class="more">READ MORE</div></div>
</section>

<!-- products -->
<section class="products" role="region" aria-label="Our products">
  <h2 class="display abs" style="top:72px;width:100%;text-align:center;font-size:46px;color:#fff">Our Products</h2>
  <div class="prod-card" style="left:112px"><div class="machine" role="img" aria-label="Blue glass-front snack vending machine" style="background:linear-gradient(90deg,#1f4fa8 0%,#2c5fb8 18%,#c9d3de 28%,#e6ebf0 60%,#aab6c4 85%,#2c5fb8 100%)"></div><h3>LOREM IPSUM</h3><p>Lorem ipsum dolor sit amet, con sectetur adipiscing.</p></div>
  <div class="prod-card" style="left:363px"><div class="machine" role="img" aria-label="Silver snack vending machine" style="background:linear-gradient(90deg,#7a7a7a 0%,#b8b8b8 18%,#e4e4e4 45%,#c0c0c0 75%,#8a8a8a 100%)"></div><h3>LOREM IPSUM</h3><p>Lorem ipsum dolor sit amet, con sectetur adipiscing.</p></div>
  <div class="prod-card" style="left:613px"><div class="machine" role="img" aria-label="Silver and blue combo vending machine" style="background:linear-gradient(90deg,#8a8a8a 0%,#cfcfcf 25%,#e8e8e8 55%,#9aa6b8 75%,#2c5fb8 85%,#1f4fa8 100%)"></div><h3>LOREM IPSUM</h3><p>Lorem ipsum dolor sit amet, con sectetur adipiscing.</p></div>
  <div class="prod-card" style="left:864px"><div class="machine" role="img" aria-label="Wide white snack vending machine" style="left:70px;width:86px;background:linear-gradient(180deg,#f2f2f2 0%,#cfd2d6 30%,#e9e9e9 60%,#b9b9b9 100%)"></div><h3>LOREM IPSUM</h3><p>Lorem ipsum dolor sit amet, con sectetur adipiscing.</p></div>
</section>

<!-- why -->
<h2 class="display abs" style="left:122px;top:2728px;font-size:46px">Why SnackOrbit?</h2>
<div class="why-text">
  <p>At SnackOrbit, we're more than vending machines; we're flavor architects, community connectors, and taste trailblazers. Imagine a world where every snack is an adventure, every sip a celebration. That's the SnackOrbit promise—a symphony of taste, convenience, and camaraderie.</p>
  <p>Our Tailored Temptations await: from salty to sweet, our snack selection dances with variety. Unwrap joy with nostalgic favorites and exotic treats.</p>
</div>
<div class="btn" style="left:112px;top:3056px;width:137px;height:51px">Learn More</div>
<div class="photo" style="left:668px;top:2663px;width:532px;height:515px;background:radial-gradient(ellipse 110px 200px at 300px 330px,#f0ece6,rgba(240,236,230,0)),radial-gradient(ellipse 90px 90px at 300px 110px,#b8b2ac,rgba(184,178,172,0)),radial-gradient(ellipse 200px 260px at 470px 220px,#8fa9a0,rgba(143,169,160,0)),linear-gradient(90deg,#1e1f22 0%,#3a3b3f 12%,#6e6258 20%,#c9bfb2 45%,#a89886 70%,#6f6a5e 100%)" role="img" aria-label="Woman selecting an item on a modern vending machine keypad"></div>

<!-- contact -->
<h2 class="display abs" style="top:3292px;width:100%;text-align:center;font-size:46px">Contact Us</h2>
<div class="field" style="left:165px;top:3378px;width:283px">Full Name</div>
<div class="field" style="left:458px;top:3378px;width:283px">Phone Number</div>
<div class="field" style="left:751px;top:3378px;width:283px">Email Address</div>
<div class="field" style="left:165px;top:3437px;width:869px;height:96px">Message...!</div>
<div class="btn" style="left:522px;top:3552px;width:155px;height:45px;font-size:14px">Submit Now</div>

<!-- call to action -->
<section class="cta" role="img" aria-label="Dim vending machine aisle in purple light">
  <h2 class="display">Ready to Experience<br>the SnackOrbit Difference?</h2>
  <p>Sign up now and let's connect. Taste the future of snacking firsthand! Contact us today and explore how our vending magic can elevate your space.</p>
  <div class="btn" style="left:463px;top:293px;width:274px;height:48px;font-size:14px">Get a Free Vending Machine</div>
</section>

<!-- footer -->
<footer class="footer">
  <svg class="abs" style="left:0;top:-30px" width="1200" height="190" viewBox="0 0 1200 190">
    <polygon points="0,0 1200,0 1200,30 600,88 0,165" fill="#1e1146"/>
    <polygon points="0,0 600,88 0,165" fill="#fff"/>
  </svg>
  <div class="abs" style="left:112px;top:196px;display:flex;align-items:center;gap:10px;font:700 38px 'Roboto',sans-serif;color:#fff"><span style="width:30px;height:30px;border-radius:50%;background:#fff;display:block"></span>SnackOrbit</div>
  <div class="f-contact" style="top:287px"><span class="ic"></span>+1 (555) 010 0199</div>
  <div class="f-contact" style="top:342px"><span class="ic"></span>hello@snackorbit.com</div>

  <div class="f-head" style="left:410px">QUICK LINKS</div>
  <div class="f-link" style="left:410px;top:230px"><span class="f-tick"></span>Home</div>
  <div class="f-link" style="left:410px;top:264px"><span class="f-tick"></span>About SnackOrbit</div>
  <div class="f-link" style="left:410px;top:297px"><span class="f-tick"></span>Why Choose SnackOrbit?</div>
  <div class="f-link" style="left:410px;top:330px"><span class="f-tick"></span>Products &amp; Services</div>
  <div class="f-link" style="left:410px;top:364px"><span class="f-tick"></span>Contact Us</div>
  <div class="f-link" style="left:633px;top:230px"><span class="f-tick"></span>Site Map</div>
  <div class="f-link" style="left:633px;top:264px"><span class="f-tick"></span>Privacy Policy</div>
  <div class="f-link" style="left:633px;top:297px"><span class="f-tick"></span>Terms Of Use</div>
  <div class="f-link" style="left:633px;top:330px"><span class="f-tick"></span>Disclaimer</div>

  <div class="f-head" style="left:810px">NEWSLETTER</div>
  <div class="abs" style="left:810px;top:230px;font-size:14px">Email</div>
  <div class="abs" style="left:810px;top:258px;width:285px;height:2px;background:#fff"></div>
  <div class="btn" style="left:810px;top:283px;width:130px;height:45px;font-size:14px">Subscribe</div>
  <div class="f-social"><span></span><span></span><span></span></div>

  <div class="abs" style="left:112px;top:420px;width:976px;height:1px;background:#333"></div>
  <div class="abs" style="top:444px;width:100%;text-align:center;font-size:13px">© 2024 <b>SnackOrbit</b> &nbsp;|&nbsp; All Rights Reserved</div>
  <span class="pay" style="left:886px"></span><span class="pay" style="left:928px"></span><span class="pay" style="left:970px"></span><span class="pay" style="left:1012px"></span><span class="pay" style="left:1050px;width:38px"></span>
</footer>

</body>
</html>
```